Brookvane Consulting Business Card Design

Business Card Design for Brookvane Consulting. Brookvane Consulting is a boutique consultancy based in Atlanta, GA., that specializes in marketing strategy, organization planning, and leadership development. We provide solutions for small businesses and startups as well as Vantage 300 companies.

http://brookvaneconsulting.com/

Target Market(s)

We provide solutions for small businesses and startups as well as Vantage 300 companies.

Industry/Entity Type

Consulting

Contact Information for Business Card

Two sided business card with priority on contact information, logo, tag line (Inspiration to Dream More, Do More, Become More)

Colors

Designer to choose colors to be used in the design.

Requirements
Must have
• contact information, logo, tag line (Inspiration to Dream More, Do More, Become More)
• Simple no over communication.
Nice to have
• I would like to see different placements of logo and creative use of both sides of the card
Should not have
• Do not put too much information on the card.

```html
<!DOCTYPE html>
<html lang="en">
<head>
<meta charset="UTF-8">
<title>Brookvane Consulting – Business Card</title>
<link href="https://fonts.googleapis.com/css2?family=Roboto:wght@400;500;700&display=swap" rel="stylesheet">
<style>
  :root {
    --backdrop: #2b2b2b;
    --card-dark: #3a3a3a;
    --card-light: #f7f7f5;
    --ink-dark: #2e2e2e;
    --ink-light: #ffffff;
    --band: #333333;
  }
  * { margin: 0; padding: 0; box-sizing: border-box; }
  html, body {
    width: 799px;
    height: 1200px;
    overflow: hidden;
    background: var(--backdrop);
    font-family: "Roboto", Arial, sans-serif;
  }
  .sheet {
    position: relative;
    width: 799px;
    height: 1200px;
  }
  .card {
    position: absolute;
    left: 100px;
    width: 600px;
    height: 343px;
    border-radius: 28px;
    overflow: hidden;
    box-shadow: 0 14px 30px rgba(0,0,0,0.45);
  }
  .card--front {
    top: 140px;
    background: var(--card-dark);
    display: flex;
    align-items: center;
    justify-content: center;
  }
  .card--back {
    top: 715px;
    background: var(--card-light);
  }
  .wordmark {
    font-weight: 700;
    letter-spacing: 0.5px;
    line-height: 1;
    display: flex;
    align-items: center;
    gap: 14px;
  }
  .wordmark__mark {
    width: 18px;
    height: 18px;
  }
  .card--front .wordmark {
    color: var(--ink-light);
    font-size: 46px;
  }
  .card--front .wordmark__mark { background: var(--ink-light); }
  .tag-band {
    position: absolute;
    left: 0;
    top: 0;
    width: 34px;
    height: 100%;
    background: var(--band);
  }
  .tag-band__text {
    position: absolute;
    left: 50%;
    top: 50%;
    transform: translate(-50%, -50%) rotate(-90deg);
    white-space: nowrap;
    color: var(--ink-light);
    font-size: 11.5px;
    letter-spacing: 0.3px;
  }
  .card--back .wordmark {
    position: absolute;
    left: 110px;
    top: 58px;
    color: var(--ink-dark);
    font-size: 34px;
  }
  .card--back .wordmark__mark { background: var(--ink-dark); width: 14px; height: 14px; }
  .contact {
    position: absolute;
    left: 62px;
    top: 180px;
    color: var(--ink-dark);
  }
  .contact__name {
    font-weight: 700;
    font-size: 22px;
    margin-bottom: 12px;
  }
  .contact__line {
    font-size: 15px;
    line-height: 1.35;
  }
</style>
</head>
<body>
  <main class="sheet">
    <section class="card card--front" aria-label="Card front">
      <div class="wordmark">
        <span class="wordmark__mark"></span>
        <span class="wordmark__name">Brookvane Consulting</span>
      </div>
    </section>

    <section class="card card--back" aria-label="Card back">
      <div class="tag-band">
        <p class="tag-band__text">Inspiration to Dream More, Do More, Become More</p>
      </div>
      <div class="wordmark">
        <span class="wordmark__mark"></span>
        <span class="wordmark__name">Brookvane Consulting</span>
      </div>
      <div class="contact">
        <p class="contact__name">Darien</p>
        <p class="contact__line">555-014-2290</p>
        <p class="contact__line">darien@brookvaneconsulting.com</p>
        <p class="contact__line">www.brookvaneconsulting.com</p>
      </div>
    </section>
  </main>
</body>
</html>
```